Tech business card design

We need an amazing business card design for our new business 'Pexla' a marketing tech startup based in Sydney, Australia. We provide an online marketplace for businesses to search and buy advertising media, connect with service providers and learn more about marketing. We wish to communicate 'cool tech', reliability and professionalism and design based around our logo.

Target Market(s)

Business Owners

Contact Information for Business Card

Name
Position
Email Address
Website
Phone Number

Font styles to use
Other font styles liked:
• Avenir & Avenir Next

Colors

Designer to choose colors to be used in the design.

```html
<!DOCTYPE html>
<html lang="en">
<head>
<meta charset="utf-8">
<title>Pexla Business Card</title>
<link rel="stylesheet" href="https://fonts.googleapis.com/css2?family=Roboto:wght@400;500;900&display=swap">
<style>
  :root {
    --navy: #121440;
    --navy-deep: #0d0f33;
    --paper: #ffffff;
    --ink: #1a1c4a;
    --muted: #6b6b78;
    --rule: #2c2d5e;
    --silver: #c9cbd4;
    --stage: #2b2b30;
  }
  * { margin: 0; padding: 0; box-sizing: border-box; }
  html, body { width: 1200px; height: 900px; overflow: hidden; }
  body {
    background: var(--stage);
    font-family: "Roboto", sans-serif;
    display: flex;
    flex-direction: column;
    align-items: center;
    justify-content: center;
    gap: 48px;
  }
  .card {
    position: relative;
    width: 630px;
    height: 360px;
    border-radius: 2px;
    box-shadow: 0 14px 30px rgba(0,0,0,0.45);
    overflow: hidden;
  }
  .card-front { background: var(--paper); }
  .card-back { background: linear-gradient(160deg, var(--navy) 0%, var(--navy-deep) 100%); }

  .wordmark {
    position: absolute;
    font-weight: 900;
    letter-spacing: -1px;
    line-height: 1;
  }
  .card-front .wordmark { right: 60px; top: 120px; font-size: 84px; color: var(--ink); }
  .card-back .wordmark { left: 50%; top: 50%; transform: translate(-50%, -50%); font-size: 110px; color: var(--silver); }

  .holder { position: absolute; left: 44px; top: 196px; }
  .holder-name { font-size: 24px; font-weight: 500; color: var(--ink); }
  .holder-role { font-size: 14px; color: var(--muted); margin-top: 2px; }

  .divider {
    position: absolute;
    left: 44px; right: 44px; top: 256px;
    height: 1.5px;
    background: var(--rule);
  }

  .contact { position: absolute; left: 44px; top: 272px; font-size: 14.5px; color: #444; line-height: 1.75; }
  .contact b { color: var(--ink); font-weight: 500; }
</style>
</head>
<body>
  <section class="card card-front">
    <div class="wordmark">Pexla</div>
    <div class="holder">
      <div class="holder-name">Daniel Reeve</div>
      <div class="holder-role">Director</div>
    </div>
    <div class="divider"></div>
    <div class="contact">
      <div><b>P</b> : +330 5180-2934 | <b>E</b> : info@pexla.com | <b>W</b> : www.pexla.com</div>
      <div><b>A</b> : 218 Larkin Avenue Dover, DE 19901</div>
    </div>
  </section>

  <section class="card card-back">
    <div class="wordmark">Pexla</div>
  </section>
</body>
</html>
```